Home page design for my business

My business will be selling templated drive-in movie theater websites. I would like my business to state to my customers that they get a free website (with hosting fees) where they can take ticket sales digitally. My company will be called Reel-Lanternworks (for Drive In Movie Theatres).

Here are some websites of my potential customers:
https://www.pelorcrest.example/
https://moonglowcinemas.example/
https://oakridgeoutdoorscreen.example/

```html
<!DOCTYPE html>
<html lang="en">
<head>
<meta charset="utf-8">
<title>Reel-Lanternworks — Free Drive-In Theatre Websites</title>
<link href="https://fonts.googleapis.com/css2?family=Jost:wght@400;500;600;700&display=swap" rel="stylesheet">
<style>
  :root {
    --night: #0b0a26;
    --ink: #000000;
    --white: #ffffff;
    --pink: #de2579;
    --indigo: #1c0f9f;
    --royal: #2a1cb3;
    --footer: #1607a2;
    --neon: #3f8cff;
    --muted: rgba(255,255,255,0.85);
  }
  * { box-sizing: border-box; margin: 0; padding: 0; }
  html, body { width: 1200px; height: 2745px; overflow: hidden; }
  body { position: relative; background: var(--ink); color: var(--white); font-family: 'Jost', sans-serif; }
  a { color: inherit; text-decoration: none; }

  /* Hero */
  .hero { position: absolute; left: 0; top: 0; width: 1200px; height: 752px; overflow: hidden; }
  .hero-scene { position: absolute; inset: 0;
    background:
      radial-gradient(ellipse 140px 420px at 600px 140px, rgba(70,80,230,0.55), transparent 70%),
      linear-gradient(180deg, #0b0a2a 0%, #14124a 45%, #2a2868 58%, #23283a 72%, #141620 100%); }
  .hero-shade { position: absolute; inset: 0; background: rgba(10,8,40,0.25); }
  .brand { position: absolute; left: 112px; top: 62px; display: flex; align-items: center; gap: 14px; }
  .brand-mark { width: 34px; height: 34px; background: var(--neon); border-radius: 6px; }
  .brand-name { font-size: 36px; font-weight: 500; color: var(--neon); letter-spacing: 0.5px; }
  .auth { position: absolute; top: 22px; right: 111px; display: flex; gap: 8px; }
  .btn-pill { display: inline-flex; align-items: center; justify-content: center; height: 48px; border-radius: 24px; font-size: 19px; font-weight: 500; }
  .btn-login { width: 130px; background: var(--pink); }
  .btn-signup { width: 130px; background: var(--indigo); }
  .main-nav { position: absolute; top: 92px; right: 111px; display: flex; gap: 42px; font-size: 20px; font-weight: 500; }
  .hero-copy { position: absolute; top: 240px; left: 0; width: 1200px; text-align: center; }
  .hero-kicker { font-size: 34px; font-weight: 500; line-height: 1.2; }
  .hero-title { font-size: 54px; font-weight: 600; line-height: 1.2; margin-top: 2px; }
  .hero-lead { font-size: 21px; line-height: 1.5; width: 580px; margin: 14px auto 0; }
  .dots { position: absolute; top: 728px; left: 0; width: 1200px; display: flex; justify-content: center; gap: 8px; }
  .dot { width: 10px; height: 10px; border-radius: 50%; background: var(--white); }
  .dot.active { background: var(--pink); }

  /* Section headings */
  .section-title { position: absolute; left: 0; width: 1200px; text-align: center; font-size: 33px; font-weight: 600; }
  .section-rule { position: absolute; left: 580px; width: 40px; height: 2px; }

  /* Now showing */
  .showing { position: absolute; left: 0; top: 752px; width: 1200px; height: 556px; background: var(--ink); }
  .showing .section-title { top: 42px; letter-spacing: 0.5px; }
  .showing .section-rule { top: 94px; background: var(--indigo); }
  .cards { position: absolute; top: 142px; left: 112px; display: flex; gap: 12px; }
  .movie-card { position: relative; width: 235px; height: 332px; border-radius: 6px; overflow: hidden; }
  .movie-art { position: absolute; inset: 0; }
  .art-lot { background: linear-gradient(180deg, #2a2436 0%, #3b3448 45%, #6b5a3e 62%, #3a3a3e 100%); }
  .art-couple { background: linear-gradient(180deg, #3b2a24 0%, #8b6a55 40%, #c9bdb1 70%, #4a3a30 100%); }
  .art-car { background: linear-gradient(180deg, #0c1a4a 0%, #3a2a9a 40%, #2a5a8a 60%, #101420 100%); }
  .art-kids { background: linear-gradient(180deg, #5a3a2a 0%, #6a7a4a 40%, #a04a3a 65%, #3a4a6a 100%); }
  .movie-info { position: absolute; left: 0; right: 0; bottom: 0; height: 110px; padding: 0 18px 18px; display: flex; flex-direction: column; justify-content: flex-end;
    background: linear-gradient(180deg, transparent, rgba(0,0,0,0.75)); }
  .movie-name { font-size: 15px; }
  .movie-meta { display: flex; align-items: center; justify-content: space-between; margin-top: 8px; font-size: 16px; font-weight: 500; }
  .movie-time { display: flex; align-items: center; gap: 7px; }

  /* Pricing banner */
  .banner { position: absolute; left: 0; top: 1308px; width: 1200px; height: 487px; overflow: hidden; }
  .banner-scene { position: absolute; inset: 0; background: linear-gradient(180deg, #2b1fb4 0%, #2a22a6 45%, #2e2aa0 70%, #2a1db6 100%); }
  .banner-copy { position: absolute; top: 110px; left: 0; width: 1200px; text-align: center; }
  .banner-title { font-size: 45px; font-weight: 600; line-height: 1.2; }
  .banner-price { font-size: 37px; line-height: 1.2; margin-top: 16px; }
  .banner-note { font-size: 30px; line-height: 1.2; margin-top: 8px; }
  .btn-outline { display: inline-flex; align-items: center; justify-content: center; width: 196px; height: 60px; border: 2px solid var(--white); border-radius: 30px; font-size: 22px; font-weight: 500; margin-top: 34px; }

  /* Ticket prices */
  .tickets { position: absolute; left: 0; top: 1795px; width: 1200px; height: 565px; overflow: hidden; }
  .tickets-scene { position: absolute; inset: 0; background: linear-gradient(180deg, #050505 0%, #0d0d12 50%, #111116 75%, #060606 100%); }
  .tickets .section-title { top: 52px; }
  .tickets .section-rule { top: 104px; background: var(--pink); }
  .ticket { position: absolute; left: 277px; top: 136px; width: 645px; height: 366px; background: var(--pink); }
  .ticket-row { display: flex; border-bottom: 1px solid rgba(255,255,255,0.18); }
  .ticket-head { height: 115px; align-items: center; }
  .ticket-prices { height: 113px; align-items: center; }
  .ticket-cell { flex: 1; text-align: center; }
  .ticket-head .ticket-cell { font-size: 20px; font-weight: 500; line-height: 1.4; }
  .ticket-prices .ticket-cell { font-size: 48px; font-weight: 600; }
  .ticket-action { text-align: center; padding-top: 28px; }
  .btn-buy { display: inline-flex; align-items: center; justify-content: center; width: 174px; height: 60px; border-radius: 30px; background: var(--indigo); font-size: 21px; font-weight: 500; }
  .ticket-edge { position: absolute; left: 0; bottom: 0; }

  /* Footer */
  .site-footer { position: absolute; left: 0; top: 2360px; width: 1200px; height: 385px; background: var(--footer); text-align: center; }
  .footer-brand { position: absolute; top: 76px; left: 0; width: 1200px; display: flex; justify-content: center; align-items: center; gap: 16px; }
  .footer-brand .brand-name { font-size: 42px; }
  .footer-brand .brand-mark { width: 40px; height: 40px; }
  .footer-nav { position: absolute; top: 178px; left: 0; width: 1200px; display: flex; justify-content: center; gap: 54px; font-size: 20px; font-weight: 500; }
  .social { position: absolute; top: 237px; left: 0; width: 1200px; display: flex; justify-content: center; gap: 6px; }
  .social-link { width: 37px; height: 37px; border: 1.5px solid var(--white); border-radius: 50%; display: flex; align-items: center; justify-content: center; }
  .social-link span { width: 10px; height: 10px; border-radius: 50%; background: var(--white); }
  .copyright { position: absolute; top: 300px; left: 0; width: 1200px; font-size: 16px; color: var(--muted); }
</style>
</head>
<body>

<header class="hero">
  <div class="hero-scene" role="img" aria-label="Drive-in theatre at night: cars parked facing a glowing outdoor screen under a starry sky with a projector beam"></div>
  <div class="hero-shade"></div>
  <a class="brand" href="#"><span class="brand-mark"></span><span class="brand-name">Reel-Lanternworks</span></a>
  <div class="auth">
    <a class="btn-pill btn-login" href="#">LOGIN</a>
    <a class="btn-pill btn-signup" href="#">SIGNUP</a>
  </div>
  <nav class="main-nav">
    <a href="#">Home</a><a href="#">About Us</a><a href="#">Shows</a><a href="#">News</a><a href="#">Contact Us</a>
  </nav>
  <div class="hero-copy">
    <p class="hero-kicker">Welcome to</p>
    <h1 class="hero-title">Reel-Lanternworks</h1>
    <p class="hero-lead">Your drive-in gets a free website, hosting included, where guests buy their tickets online in seconds</p>
  </div>
  <div class="dots"><span class="dot"></span><span class="dot active"></span><span class="dot"></span></div>
</header>

<section class="showing">
  <h2 class="section-title">NOW SHOWING</h2>
  <div class="section-rule"></div>
  <div class="cards">
    <article class="movie-card">
      <div class="movie-art art-lot" role="img" aria-label="Cars parked at a drive-in lot at dusk facing the screen"></div>
      <div class="movie-info">
        <p class="movie-name">Sed ut perspiciatis unde</p>
        <div class="movie-meta"><span class="movie-time"><svg width="14" height="14" viewBox="0 0 14 14"><circle cx="7" cy="7" r="5.8" fill="none" stroke="#fff" stroke-width="1.8"/><path d="M7 4v3.3l2 1.3" fill="none" stroke="#fff" stroke-width="1.6"/></svg>7:45</span><svg width="16" height="14" viewBox="0 0 16 14"><path d="M8 13.5 1.6 7.4A3.8 3.8 0 0 1 8 2.6a3.8 3.8 0 0 1 6.4 4.8Z" fill="#de2579"/></svg></div>
      </div>
    </article>
    <article class="movie-card">
      <div class="movie-art art-couple" role="img" aria-label="Two friends sharing popcorn in the back of a car"></div>
      <div class="movie-info">
        <p class="movie-name">Sed ut perspiciatis unde</p>
        <div class="movie-meta"><span class="movie-time"><svg width="14" height="14" viewBox="0 0 14 14"><circle cx="7" cy="7" r="5.8" fill="none" stroke="#fff" stroke-width="1.8"/><path d="M7 4v3.3l2 1.3" fill="none" stroke="#fff" stroke-width="1.6"/></svg>9:35</span><svg width="16" height="14" viewBox="0 0 16 14"><path d="M8 13.5 1.6 7.4A3.8 3.8 0 0 1 8 2.6a3.8 3.8 0 0 1 6.4 4.8Z" fill="#de2579"/></svg></div>
      </div>
    </article>
    <article class="movie-card">
      <div class="movie-art art-car" role="img" aria-label="Classic car in front of a neon-lit building at night"></div>
      <div class="movie-info">
        <p class="movie-name">Sed ut perspiciatis unde</p>
        <div class="movie-meta"><span class="movie-time"><svg width="14" height="14" viewBox="0 0 14 14"><circle cx="7" cy="7" r="5.8" fill="none" stroke="#fff" stroke-width="1.8"/><path d="M7 4v3.3l2 1.3" fill="none" stroke="#fff" stroke-width="1.6"/></svg>Coming Soon</span><svg width="16" height="14" viewBox="0 0 16 14"><path d="M8 13.5 1.6 7.4A3.8 3.8 0 0 1 8 2.6a3.8 3.8 0 0 1 6.4 4.8Z" fill="#de2579"/></svg></div>
      </div>
    </article>
    <article class="movie-card">
      <div class="movie-art art-kids" role="img" aria-label="Children in cardboard box cars at an outdoor movie party"></div>
      <div class="movie-info">
        <p class="movie-name">Sed ut perspiciatis unde</p>
        <div class="movie-meta"><span class="movie-time"><svg width="14" height="14" viewBox="0 0 14 14"><circle cx="7" cy="7" r="5.8" fill="none" stroke="#fff" stroke-width="1.8"/><path d="M7 4v3.3l2 1.3" fill="none" stroke="#fff" stroke-width="1.6"/></svg>Coming Soon</span><svg width="16" height="14" viewBox="0 0 16 14"><path d="M8 13.5 1.6 7.4A3.8 3.8 0 0 1 8 2.6a3.8 3.8 0 0 1 6.4 4.8Z" fill="#de2579"/></svg></div>
      </div>
    </article>
  </div>
</section>

<section class="banner">
  <div class="banner-scene" role="img" aria-label="Blue-tinted drive-in screen with parked cars"></div>
  <div class="banner-copy">
    <h2 class="banner-title">A Fun Night Out For Everyone!</h2>
    <p class="banner-price">$10.00 Per Person Children 6 - 12 $ 1.00</p>
    <p class="banner-note">Kids 5 and Under Free</p>
    <a class="btn-outline" href="#">View Details</a>
  </div>
</section>

<section class="tickets">
  <div class="tickets-scene" role="img" aria-label="Dim drive-in lot with cars in the dark"></div>
  <h2 class="section-title">Ticket Prices</h2>
  <div class="section-rule"></div>
  <div class="ticket">
    <div class="ticket-row ticket-head">
      <div class="ticket-cell">General<br>Admissions</div>
      <div class="ticket-cell">Children<br>5-11 Years Old</div>
      <div class="ticket-cell">Under<br>5 Years Old</div>
    </div>
    <div class="ticket-row ticket-prices">
      <div class="ticket-cell">$10</div>
      <div class="ticket-cell">$3.50</div>
      <div class="ticket-cell">Free</div>
    </div>
    <div class="ticket-action"><a class="btn-buy" href="#">Buy Tickets</a></div>
    <svg class="ticket-edge" width="645" height="20" viewBox="0 0 645 20">
      <g fill="#000">
        <circle cx="31" cy="20" r="18"/><circle cx="76" cy="20" r="18"/><circle cx="121" cy="20" r="18"/><circle cx="166" cy="20" r="18"/><circle cx="211" cy="20" r="18"/><circle cx="256" cy="20" r="18"/><circle cx="301" cy="20" r="18"/><circle cx="346" cy="20" r="18"/><circle cx="391" cy="20" r="18"/><circle cx="436" cy="20" r="18"/><circle cx="481" cy="20" r="18"/><circle cx="526" cy="20" r="18"/><circle cx="571" cy="20" r="18"/><circle cx="616" cy="20" r="18"/>
      </g>
    </svg>
  </div>
</section>

<footer class="site-footer">
  <a class="footer-brand" href="#"><span class="brand-mark"></span><span class="brand-name">Reel-Lanternworks</span></a>
  <nav class="footer-nav">
    <a href="#">Home</a><a href="#">About Us</a><a href="#">Shows</a><a href="#">News</a><a href="#">Contact Us</a>
  </nav>
  <div class="social">
    <a class="social-link" href="#" aria-label="Social link 1"><span></span></a>
    <a class="social-link" href="#" aria-label="Social link 2"><span></span></a>
    <a class="social-link" href="#" aria-label="Social link 3"><span></span></a>
    <a class="social-link" href="#" aria-label="Social link 4"><span></span></a>
    <a class="social-link" href="#" aria-label="Social link 5"><span></span></a>
  </div>
  <p class="copyright">© Copyright 2022 Reel-Lanternworks.All Rights Reserved</p>
</footer>

</body>
</html>
```